Heron Loan Partners Business Card

We need a business card design for our mortgage servicing company. In addition to servicing the loans of homeowners, we help homeowners with purchasing their homes and any mortgage refinancing. We would like to see designs that use the colors in the logo attached below (gold-ish yellow and navy blue), and any other design you deem fit! The design should communicate a simpler life with smart mortgages provided by Heron.

```html
<!DOCTYPE html>
<html lang="en">
<head>
<meta charset="UTF-8">
<title>Heron Loan Partners Business Card</title>
<link href="https://fonts.googleapis.com/css2?family=Montserrat:wght@700&family=Open+Sans:wght@400;600;700&display=swap" rel="stylesheet">
<style>
  :root {
    --bg: #232323;
    --card: #ffffff;
    --gold: #e0b03e;
    --navy: #252056;
    --ink: #1b1b1b;
  }
  * { margin: 0; padding: 0; box-sizing: border-box; }
  html, body { width: 1200px; height: 780px; overflow: hidden; }
  body {
    background: var(--bg);
    font-family: "Open Sans", Arial, sans-serif;
    color: var(--ink);
    position: relative;
  }
  .card {
    position: absolute;
    top: 235px;
    width: 540px;
    height: 310px;
    background: var(--card);
    border-radius: 18px;
    box-shadow: 0 0 0 3px var(--gold), 0 14px 30px rgba(0,0,0,.55);
    overflow: hidden;
  }
  .card--front { left: 35px; }
  .card--back { left: 625px; }

  .wordmark {
    font-family: "Open Sans", Arial, sans-serif;
    font-weight: 700;
    color: var(--gold);
    line-height: 1.05;
    text-align: center;
  }
  .card--front .wordmark {
    position: absolute;
    inset: 0;
    display: flex;
    align-items: center;
    justify-content: center;
    font-size: 46px;
  }
  .card--back .wordmark {
    position: absolute;
    left: 30px;
    top: 100px;
    width: 190px;
    font-size: 28px;
  }

  .divider {
    position: absolute;
    left: 248px;
    top: 52px;
    width: 1.5px;
    height: 160px;
    background: var(--ink);
  }

  .details {
    position: absolute;
    left: 272px;
    top: 40px;
    width: 260px;
  }
  .name {
    font-family: "Montserrat", Arial, sans-serif;
    font-weight: 700;
    font-size: 22px;
    line-height: 1.1;
  }
  .name__first { color: var(--gold); }
  .name__last { color: var(--navy); }
  .role {
    font-weight: 600;
    font-size: 12.5px;
    margin-top: 3px;
  }
  .address {
    font-size: 12.5px;
    line-height: 1.35;
    margin-top: 14px;
  }
  .contact-list {
    list-style: none;
    margin-top: 14px;
    font-size: 12.5px;
    line-height: 1.35;
  }
  .contact-list li {
    display: flex;
    align-items: center;
    gap: 7px;
    margin-bottom: 2px;
  }
  .contact-list svg { width: 13px; height: 13px; flex: none; }

  .band { position: absolute; }
  .band--gold { left: 0; bottom: 18px; }
  .band--navy { right: 0; bottom: 52px; }
</style>
</head>
<body>

  <section class="card card--front">
    <div class="wordmark">Heron Loan<br>Partners</div>
  </section>

  <section class="card card--back">
    <div class="wordmark">Heron Loan<br>Partners</div>

    <div class="divider"></div>

    <div class="details">
      <h1 class="name"><span class="name__first">Lena</span> <span class="name__last">Varga</span></h1>
      <p class="role">Managing Director</p>
      <p class="address">418 Willowbend Ave. Suite<br>310 Dallas, TX 75201</p>
      <ul class="contact-list">
        <li>
          <svg viewBox="0 0 16 16" aria-hidden="true"><path fill="var(--gold)" d="M3.5 1.5l2.5 0 1 3.5-1.7 1.2a8 8 0 0 0 4.5 4.5l1.2-1.7 3.5 1v2.5c0 .8-.7 1.5-1.5 1.5C6.8 14 2 9.2 2 3c0-.8.7-1.5 1.5-1.5z"/></svg>
          (555) 214-6630
        </li>
        <li>
          <svg viewBox="0 0 16 16" aria-hidden="true"><rect x="1" y="3" width="14" height="10" rx="1.5" fill="var(--gold)"/><path d="M1.5 4l6.5 5 6.5-5" fill="none" stroke="#fff" stroke-width="1.3"/></svg>
          info@heronloans.com
        </li>
        <li>
          <svg viewBox="0 0 16 16" aria-hidden="true"><circle cx="8" cy="8" r="7" fill="var(--gold)"/><path d="M1 8h14M8 1c-3 3.5-3 10.5 0 14M8 1c3 3.5 3 10.5 0 14" fill="none" stroke="#fff" stroke-width="1"/></svg>
          www.heronloans.com
        </li>
      </ul>
    </div>

    <svg class="band band--navy" width="230" height="22" viewBox="0 0 230 22" aria-hidden="true">
      <path d="M0 0H230V22H30Q10 22 0 0Z" fill="var(--navy)"/>
    </svg>
    <svg class="band band--gold" width="340" height="26" viewBox="0 0 340 26" aria-hidden="true">
      <path d="M0 0H320Q330 0 340 0L326 26H0Z" fill="var(--gold)"/>
    </svg>
  </section>

</body>
</html>
```